Redesign of business card for Cedar Ridge Mechanical

We are looking for a new design for our business cards for Cedar Ridge Mechanical. We are a plumbing & HVAC construction company, operating on the West Coast of Canada and USA. Logo attached.
Industry/Entity Type
Construction - Plumbing & HVAC
Contact Information for Business Card
Name, address, phone numbers, email, website address
Look and feel
Each slider illustrates characteristics of the customer's brand and the style your logo design should communicate.

```html
<!DOCTYPE html>
<html lang="en">
<head>
<meta charset="utf-8">
<title>Cedar Ridge Mechanical — Business Card</title>
<link href="https://fonts.googleapis.com/css2?family=Poppins:wght@300;400;600;700&display=swap" rel="stylesheet">
<style>
  :root {
    --backdrop: #1f1f20;
    --card: #232325;
    --ink: #ffffff;
    --ink-soft: #d9d9d9;
    --band-text: #1b1b1b;
  }
  * { box-sizing: border-box; margin: 0; padding: 0; }
  html, body {
    width: 1200px; height: 711px; overflow: hidden;
    background: var(--backdrop);
    font-family: "Poppins", sans-serif;
    color: var(--ink);
  }
  .stage { position: relative; width: 1200px; height: 711px; }
  .card {
    position: absolute;
    width: 540px; height: 309px;
    background: var(--card);
    border-radius: 24px;
    overflow: hidden;
    box-shadow: 0 0 0 2px #3a3a3c, 0 18px 40px rgba(0,0,0,.6);
  }
  .card--front { left: 90px; top: 50px; }
  .card--back { left: 570px; top: 350px; }

  .brand { display: flex; align-items: center; gap: 14px; }
  .brand__mark { border: 4px solid var(--ink); border-radius: 4px; flex: none; }
  .brand__name {
    font-weight: 600; text-transform: uppercase; letter-spacing: 2px; line-height: 1.1;
  }
  .card--front .brand {
    position: absolute; left: 50%; top: 50%; transform: translate(-50%, -50%);
  }
  .card--front .brand__mark { width: 54px; height: 54px; }
  .card--front .brand__name { font-size: 26px; }

  .back__brand { position: absolute; left: 34px; top: 86px; }
  .back__brand .brand__mark { width: 36px; height: 36px; border-width: 3px; }
  .back__brand .brand__name { font-size: 16px; letter-spacing: 1.5px; }

  .divider {
    position: absolute; left: 232px; top: 30px; width: 1px; height: 180px;
    background: var(--ink-soft); opacity: .7;
  }

  .person { position: absolute; left: 262px; top: 40px; }
  .person__name { font-size: 26px; line-height: 1.1; }
  .person__first { font-weight: 700; }
  .person__last { font-weight: 300; }
  .person__title { font-size: 12px; font-weight: 400; margin-top: 4px; }

  .contacts { position: absolute; left: 278px; top: 118px; list-style: none; }
  .contacts li {
    display: flex; align-items: center; gap: 10px;
    font-size: 12.5px; font-weight: 300; margin-bottom: 7px;
  }
  .contacts svg { width: 13px; height: 13px; fill: var(--ink); flex: none; }

  .address-band {
    position: absolute; left: 0; right: 0; bottom: 36px; height: 26px;
    background: var(--ink); color: var(--band-text);
    display: flex; align-items: center; padding-left: 60px;
    font-size: 13px; font-weight: 400;
  }
  .band-brand {
    position: absolute; right: 28px; bottom: 48px;
    background: var(--card); padding: 6px 8px; border: 3px solid var(--ink); border-radius: 8px;
  }
  .band-brand .brand { gap: 6px; }
  .band-brand .brand__mark { width: 14px; height: 14px; border-width: 2px; border-radius: 2px; }
  .band-brand .brand__name { font-size: 9px; letter-spacing: 1px; }
</style>
</head>
<body>
<main class="stage">

  <section class="card card--front" aria-label="Card front">
    <div class="brand">
      <span class="brand__mark"></span>
      <span class="brand__name">Cedar Ridge<br>Mechanical</span>
    </div>
  </section>

  <section class="card card--back" aria-label="Card back">
    <div class="brand back__brand">
      <span class="brand__mark"></span>
      <span class="brand__name">Cedar Ridge<br>Mechanical</span>
    </div>

    <div class="divider"></div>

    <div class="person">
      <p class="person__name"><span class="person__first">Marta</span> <span class="person__last">Kovalenko</span></p>
      <p class="person__title">Founder &amp; CEO</p>
    </div>

    <ul class="contacts">
      <li>
        <svg viewBox="0 0 24 24" aria-hidden="true"><path d="M6.6 10.8a15 15 0 0 0 6.6 6.6l2.2-2.2c.3-.3.7-.4 1-.2 1.1.4 2.3.6 3.6.6.6 0 1 .4 1 1V20c0 .6-.4 1-1 1A17 17 0 0 1 3 4c0-.6.4-1 1-1h3.5c.6 0 1 .4 1 1 0 1.3.2 2.5.6 3.6.1.3 0 .7-.2 1z"/></svg>
        (604) 555-0187
      </li>
      <li>
        <svg viewBox="0 0 24 24" aria-hidden="true"><path d="M2 5h20v14H2zm2 2v.5l8 5 8-5V7zm0 2.8V17h16V9.8l-8 5z"/></svg>
        info@cedarridgemech.com
      </li>
      <li>
        <svg viewBox="0 0 24 24" aria-hidden="true"><path d="M12 2a10 10 0 1 0 0 20 10 10 0 0 0 0-20zm6.9 6h-3a15 15 0 0 0-1.3-3.9A8 8 0 0 1 18.9 8zM12 4c.8 1.2 1.5 2.5 1.9 4h-3.8c.4-1.5 1.1-2.8 1.9-4zM4.3 14a8 8 0 0 1 0-4h3.4a16 16 0 0 0 0 4zm.8 2h3a15 15 0 0 0 1.3 3.9A8 8 0 0 1 5.1 16zm3-8h-3a8 8 0 0 1 4.3-3.9A15 15 0 0 0 8.1 8zM12 20c-.8-1.2-1.5-2.5-1.9-4h3.8c-.4 1.5-1.1 2.8-1.9 4zm2.3-6H9.7a14 14 0 0 1 0-4h4.6a14 14 0 0 1 0 4zm.3 5.9c.6-1.2 1-2.5 1.3-3.9h3a8 8 0 0 1-4.3 3.9zm1.7-5.9a16 16 0 0 0 0-4h3.4a8 8 0 0 1 0 4z"/></svg>
        www.cedarridgemech.com
      </li>
    </ul>

    <div class="address-band">418 Harbor Lane Suite 120 Portland, OR 97201</div>

    <div class="band-brand">
      <div class="brand">
        <span class="brand__mark"></span>
        <span class="brand__name">Cedar Ridge</span>
      </div>
    </div>
  </section>

</main>
</body>
</html>
```